Marigold Synchronized Swim Team's Clubhouse (web page)

Fun, Super Easy to read and navigate. Please error on the side of too large font sizes rather than too small font sizes.

We are a New Orleans (USA) based club for adults and youth of all genders.

We have youth and adult performance and competition teams. We teach synchronized swimming. We perform at special events.

Webpage should allow for

1. Sign up for classes, camps and teams (pay fees, sign waivers, reserve a spot and link to national Delmar Aquaform club membership website in order to buy required national membership).Make our multi step registration process easy, quick, pleasant.

2. Provide an area to upload practice schedules.
and performance calendar.

3. Easily
Hire one of our synchro squad to perform at special events.

4. Embedded Google Calndar

5 Members only site
( one away for youth and one area for adults. )

6 Show off our new logo, photos and videos. Be able to change these images often.

Our team colors are red, aqua and pink.

7. Buy logo gear

Click to team shop at
Brindle cove.com and other future team shops.

8. One click to become a sponsor of the team.

An area to show off sponsor logos. We will have several levels of sponsorships. It is important to have small medium and large logo spots. WE also will have a wall of names of folks who donate 10 - 100 dollars to sponsor the team.

We want the experience to be fun . We do not want headache producing events.

Our team colors are red, pink and aqua. WE have not settled on a specific red or pink yet. You are free to play around with different tones and hues. I tend toward a sholcking pink and cherry red. But really do want to see what your thoughts are for our reds and pinks. Also feel free to vary aqua from a light to dark. But we do want to stay away from navy.
Thanks for your hard work and creativity.

Target Market(s)

All ages, genders and ethnicity. Swimmers, dancers and event planners.

Coding

Coded - Design and coding required

Number of Pages Required

4 page

Font styles to use
Sans Serif

Colors
ec1f27
0293ce
f59195

Requirements
Must have
• See p descriptions +
• Fine #20 is our logo and
• Playful, bold, elegant, Colorful (red, aqua and pink are our team colors).
• I want to be able to plug in / update photos , schedules, release forms, almost everything as our seasons change. I do not know ( Newbury) do I want coded or incised site. All advice welcome.
Nice to have
• Your flare as a designer. Thank you for making us better through your creativity, ability to edit, clarify and advice. :-)
Should not have
• Confusion.

```html
<!DOCTYPE html>
<html lang="en">
<head>
<meta charset="utf-8">
<title>Tidewell LLC – Marigold Synchronized Swim Team</title>
<link href="https://fonts.googleapis.com/css2?family=Exo+2:wght@500;600;700&family=Open+Sans:wght@400;600;700&display=swap" rel="stylesheet">
<style>
:root{
  --aqua:#0293ce;
  --aqua-dark:#0a7fb4;
  --red:#ec1f27;
  --pink:#f59195;
  --ink:#333;
  --muted:#777;
  --light:#f5f6f7;
  --line:#e4e4e4;
  --white:#fff;
}
*{box-sizing:border-box;margin:0;padding:0}
html,body{width:1200px;height:2844px;overflow:hidden}
body{font-family:"Open Sans",Arial,sans-serif;color:var(--ink);background:var(--white);position:relative}
.heading{font-family:"Exo 2",Arial,sans-serif;font-weight:700;text-transform:uppercase;color:var(--aqua);letter-spacing:.5px}
.wrap{width:1030px;margin:0 auto;position:relative}

/* top bar */
.topbar{height:52px;background:var(--aqua);color:var(--white)}
.topbar .wrap{display:flex;justify-content:space-between;align-items:center;height:52px}
.social{display:flex;gap:9px}
.social span{width:28px;height:28px;border:2px solid var(--white);border-radius:50%;display:block}
.contact-line{display:flex;gap:34px;font-size:14px;font-weight:600}
.contact-line span{display:flex;align-items:center;gap:8px}

/* nav */
.nav{height:83px;background:var(--white);position:relative;z-index:3}
.nav .wrap{height:83px;display:flex;justify-content:flex-end;align-items:center}
.brand{position:absolute;left:0;top:-6px;width:150px;height:150px;border-radius:50%;background:var(--white);display:flex;flex-direction:column;align-items:center;justify-content:center;text-align:center}
.brand-mark{width:26px;height:26px;border-radius:50%;background:var(--pink);margin-bottom:6px}
.brand-name{font-family:"Exo 2",sans-serif;font-weight:700;font-size:17px;color:var(--aqua-dark)}
.brand-sub{font-size:8px;color:var(--aqua-dark);width:120px;margin-top:3px}
.menu{display:flex;gap:50px;font-size:13px;font-weight:600;text-transform:uppercase;align-items:center}
.menu a{color:#444;text-decoration:none}
.menu a.active{color:var(--aqua)}
.search{width:42px;height:42px;border:2px solid var(--aqua);border-radius:50%;display:flex;align-items:center;justify-content:center;margin-left:-18px}

/* hero */
.hero{height:495px;position:relative;overflow:hidden;background:linear-gradient(160deg,#7d8a93 0%,#a9b3b9 28%,#3fa9d6 52%,#4f97bd 72%,#6b7f8c 100%)}
.hero-copy{position:absolute;left:680px;top:195px;width:440px;color:var(--white)}
.hero-copy h1{font-family:"Exo 2",sans-serif;font-size:34px;font-weight:700;margin-bottom:16px;text-shadow:0 1px 3px rgba(0,0,0,.35)}
.hero-copy p{font-size:12px;line-height:20px;text-shadow:0 1px 2px rgba(0,0,0,.45)}
.hero-actions{position:absolute;left:680px;top:348px;display:flex;gap:6px}
.btn{display:inline-block;padding:0 12px;height:42px;line-height:42px;color:var(--white);font-size:13px;font-weight:700;text-transform:uppercase;border-radius:3px}
.btn-aqua{background:var(--aqua)}
.btn-red{background:var(--red)}
.dots{position:absolute;right:48px;top:457px;display:flex;gap:4px}
.dots span{width:14px;height:14px;border-radius:50%;border:2px solid var(--white)}
.dots span.on{background:var(--red)}

/* welcome */
.welcome{height:426px}
.welcome .wrap{display:flex;justify-content:space-between;padding-top:53px}
.welcome-text{width:490px}
.welcome-text h2{font-size:25px;margin-bottom:24px}
.welcome-text p{font-size:12px;line-height:24px;color:#555;margin-bottom:16px}
.welcome-text .btn{margin-top:18px;height:40px;line-height:40px;padding:0 16px}
.video{width:510px;height:316px;background:linear-gradient(135deg,#1d96b8,#2ab8c9 50%,#1685a8);position:relative;display:flex;align-items:center;justify-content:center}

/* blog */
.blog{height:514px;background:var(--light);text-align:center;padding-top:38px}
.section-intro{font-size:12px;line-height:22px;color:#666;width:760px;margin:14px auto 0}
.section-title{font-size:26px}
.posts{display:flex;justify-content:space-between;margin-top:40px;text-align:left}
.post{width:328px}
.post-photo{height:193px;position:relative}
.date{position:absolute;left:0;bottom:0;width:70px;height:70px;background:var(--red);color:var(--white);text-align:center;padding-top:13px;font-size:20px;line-height:22px}
.date small{display:block;font-size:15px}
.post h3{font-size:17px;font-weight:600;color:#555;margin:18px 0 12px}
.post p{font-size:12px;line-height:22px;color:#666}

/* events */
.events{height:487px;background:linear-gradient(160deg,#2aa2d8,#0b84c6 45%,#1e9ed8 70%,#0a7bbf)}
.events .wrap{display:flex;justify-content:space-between;padding-top:38px}
.calendar{width:603px;height:413px;background:var(--white);border-radius:5px;padding:28px 48px 0;position:relative}
.cal-head{display:flex;justify-content:space-between;align-items:center;font-family:"Exo 2",sans-serif}
.cal-head .yr{color:var(--aqua);font-weight:700;font-size:15px}
.cal-head .mo{color:#555;font-size:21px;font-weight:600}
.calendar table{width:100%;border-collapse:collapse;margin-top:44px;text-align:center}
.calendar th{font-size:19px;font-weight:600;color:#333;padding-bottom:28px}
.calendar td{font-size:14px;height:41px;color:#333}
.today{display:inline-block;width:28px;height:28px;line-height:28px;border-radius:50%;background:var(--aqua);color:var(--white);font-weight:700}
.cal-arrow{position:absolute;top:240px;width:16px;height:16px;border-radius:50%;background:#aaa}
.cal-badge{position:absolute;right:24px;bottom:14px;font-size:17px;font-weight:600;color:#555}
.event-list{width:400px;color:var(--white)}
.event-top{display:flex;justify-content:space-between;align-items:center;margin-bottom:26px}
.event-top h2{font-family:"Exo 2",sans-serif;font-size:25px;font-weight:700;letter-spacing:.5px;text-transform:uppercase}
.pager{display:flex;gap:4px}
.pager span{width:26px;height:26px;border:2px solid var(--white);border-radius:50%}
.event{display:flex;gap:22px;margin-bottom:43px}
.event-date{width:66px;height:66px;flex:none;border:2px solid var(--white);border-radius:50%;text-align:center;padding-top:10px;font-size:22px;line-height:22px}
.event-date small{display:block;font-size:13px}
.event h4{font-size:13px;font-weight:700;text-transform:uppercase;margin-bottom:8px}
.event p{font-size:11px;line-height:19px}

/* sponsors */
.sponsors{height:461px;text-align:center;padding-top:40px}
.sponsor-grid{display:grid;grid-template-columns:repeat(5,206px);margin-top:42px}
.sponsor{height:133px;display:flex;align-items:center;justify-content:center;gap:8px;font-size:22px;font-weight:600;color:#a4a4a4;border-right:1px solid var(--line);border-bottom:1px solid var(--line)}
.sponsor:nth-child(5n){border-right:none}
.sponsor:nth-child(n+6){border-bottom:none}
.sponsor i{width:14px;height:14px;border-radius:50%;background:#c4c4c4}

/* footer */
.footer{height:262px;background:var(--light)}
.footer .wrap{display:flex;padding-top:40px}
.footer-brand{width:270px;display:flex;flex-direction:column;align-items:center;padding-top:26px}
.footer-brand .brand-mark{width:40px;height:40px}
.footer-brand .brand-name{font-size:22px}
.footer-brand .brand-sub{font-size:9px;width:170px}
.footer-col h5{font-family:"Exo 2",sans-serif;font-size:16px;font-weight:600;text-transform:uppercase;color:#333;margin-bottom:26px}
.col-contact{width:262px}
.col-news{width:268px}
.col-follow{width:230px}
.contact-item{display:flex;gap:12px;align-items:flex-start;font-size:11px;color:#555;margin-bottom:12px;line-height:16px}
.contact-item a{color:#555}
.col-news p,.col-follow p{font-size:11px;line-height:18px;color:#555}
.field{width:214px;height:32px;border:1px solid #ddd;background:var(--white);margin:16px 0 12px;font-size:11px;color:#666;padding:8px 10px}
.btn-small{display:inline-block;background:var(--red);color:var(--white);font-size:10px;font-weight:700;padding:6px 9px;text-transform:uppercase}
.follow-icons{display:flex;gap:9px;margin-top:16px}
.follow-icons span{width:34px;height:34px;border:1px solid #bbb;border-radius:50%}
.copyright{height:64px;background:var(--aqua);color:var(--white);text-align:center;line-height:64px;font-size:12px}
</style>
</head>
<body>

<header class="topbar">
  <div class="wrap">
    <div class="social"><span></span><span></span><span></span><span></span><span></span></div>
    <div class="contact-line">
      <span><svg width="14" height="11" viewBox="0 0 14 11"><rect x="0.5" y="0.5" width="13" height="10" fill="none" stroke="#fff"/><path d="M1 1l6 5 6-5" fill="none" stroke="#fff"/></svg>EMAIL : info@tidewellclub.com</span>
      <span><svg width="12" height="12" viewBox="0 0 12 12"><path d="M2 1l2.5 0 1 3-1.5 1a7 7 0 0 0 3 3l1-1.5 3 1V11A10 10 0 0 1 1 2z" fill="#fff"/></svg>CALL US : (504)-555-0148</span>
    </div>
  </div>
</header>

<nav class="nav">
  <div class="wrap">
    <div class="brand">
      <span class="brand-mark"></span>
      <span class="brand-name">TIDEWELL</span>
      <span class="brand-sub">Marigold Synchronized Swim Team</span>
    </div>
    <div class="menu">
      <a class="active">Home</a><a>About Us</a><a>Services</a><a>Events</a><a>News</a><a>Sponsor</a><a>Contact Us</a>
      <span class="search"><svg width="14" height="14" viewBox="0 0 14 14"><circle cx="6" cy="6" r="4.5" fill="none" stroke="#0293ce" stroke-width="2"/><path d="M9.5 9.5L13 13" stroke="#0293ce" stroke-width="2"/></svg></span>
    </div>
  </div>
</nav>

<section class="hero" role="img" aria-label="Photo of synchronized swimmers raising their legs in a pool as spectators watch from the deck">
  <div class="hero-copy">
    <h1>TIDEWELL LLC</h1>
    <p>Synchronized swimming classes, camps and competition teams for youth and adults of all genders, right here in New Orleans. Join the squad today.</p>
  </div>
  <div class="hero-actions">
    <span class="btn btn-aqua">Become a Sponsor</span>
    <span class="btn btn-red">Team Shops</span>
  </div>
  <div class="dots"><span></span><span></span><span class="on"></span><span></span><span></span></div>
</section>

<section class="welcome">
  <div class="wrap">
    <div class="welcome-text">
      <h2 class="heading">Welcome to Tidewell LLC</h2>
      <p>We are a New Orleans club that teaches synchronized swimming to swimmers of every age. Our youth and adult teams train, compete and perform all year, and new swimmers are always welcome to try a class with our friendly coaches before they commit to a full season.</p>
      <p>Book our synchro squad for your next party, festival or special event. We bring music, color and a splash of sparkle to every pool we visit.</p>
      <span class="btn btn-aqua">Upload Practice Schedules</span>
    </div>
    <div class="video" role="img" aria-label="Video still of young swimmers in caps and goggles looking up from the pool">
      <svg width="74" height="74" viewBox="0 0 74 74"><circle cx="37" cy="37" r="35" fill="rgba(0,0,0,.25)" stroke="#fff" stroke-width="3"/><path d="M30 24l20 13-20 13z" fill="#fff"/></svg>
    </div>
  </div>
</section>

<section class="blog">
  <div class="wrap">
    <h2 class="heading section-title">Recent Blog</h2>
    <p class="section-intro">Catch up with the latest news from practice, meets and shows. Our swimmers share stories, photos and tips from every corner of the season.</p>
    <div class="posts">
      <article class="post">
        <div class="post-photo" role="img" aria-label="Photo of three swimmers in red caps and suits at the pool edge" style="background:linear-gradient(135deg,#b3454d,#d9707a 50%,#8a3a40)"><div class="date">20<small>DEC</small></div></div>
        <h3>Splash into the new season</h3>
        <p>Our fall tryouts brought so many new faces to the pool. Here is how the first weeks of training went for every team.</p>
      </article>
      <article class="post">
        <div class="post-photo" role="img" aria-label="Photo of swimmers practicing laps in a bright outdoor pool" style="background:linear-gradient(160deg,#8fa0a8,#38b8e6 40%,#5fd0f0)"><div class="date">20<small>DEC</small></div></div>
        <h3>Meet day recap and results</h3>
        <p>Our youth squad swam strong routines at the regional meet and came home with ribbons, smiles and plenty of new goals.</p>
      </article>
      <article class="post">
        <div class="post-photo" role="img" aria-label="Photo of a swimmer floating on her back with one leg raised" style="background:linear-gradient(160deg,#3fb2cf,#26a3c4 50%,#4fc3d8)"><div class="date">20<small>DEC</small></div></div>
        <h3>Five tips for better ballet legs</h3>
        <p>Coach shares simple drills that build height, balance and control so every swimmer can hold that perfect leg a little longer.</p>
      </article>
    </div>
  </div>
</section>

<section class="events" role="img" aria-label="Background photo of rippling blue pool water">
  <div class="wrap">
    <div class="calendar">
      <div class="cal-head"><span class="yr">2015</span><span class="mo">DECEMBER, 2016</span><span class="yr">2016</span></div>
      <table>
        <tr><th>SUN</th><th>MON</th><th>TUE</th><th>WED</th><th>THUR</th><th>FRI</th><th>SAT</th></tr>
        <tr><td>1</td><td>2</td><td>3</td><td>4</td><td>5</td><td>6</td><td>7</td></tr>
        <tr><td>8</td><td><span class="today">9</span></td><td>10</td><td>11</td><td>12</td><td>13</td><td>14</td></tr>
        <tr><td>15</td><td>16</td><td>17</td><td>18</td><td>19</td><td>20</td><td>21</td></tr>
        <tr><td>22</td><td>23</td><td>24</td><td>25</td><td>26</td><td>27</td><td>28</td></tr>
        <tr><td>29</td><td>30</td><td>31</td><td></td><td></td><td></td><td></td></tr>
      </table>
      <span class="cal-arrow" style="left:16px"></span>
      <span class="cal-arrow" style="right:16px"></span>
      <span class="cal-badge">Planly</span>
    </div>
    <div class="event-list">
      <div class="event-top"><h2>Special Events</h2><div class="pager"><span></span><span></span></div></div>
      <div class="event"><div class="event-date">05<small>DEC</small></div><div><h4>Holiday water show at City Park</h4><p>Join our youth and adult teams for a festive evening show with music and lights.</p></div></div>
      <div class="event"><div class="event-date">15<small>DEC</small></div><div><h4>Open house and free try-out class</h4><p>Bring a swimsuit and meet the coaches, learn basic sculls and tour the clubhouse.</p></div></div>
      <div class="event"><div class="event-date">28<small>DEC</small></div><div><h4>Winter camp registration closes</h4><p>Reserve a spot, sign the waiver and pay camp fees online before spots fill up.</p></div></div>
    </div>
  </div>
</section>

<section class="sponsors">
  <div class="wrap">
    <h2 class="heading section-title">Our Sponsor</h2>
    <p class="section-intro">Our sponsors keep our swimmers in the water. Thank you to every business and family that supports lessons, travel, costumes and shows.</p>
    <div class="sponsor-grid">
      <div class="sponsor">Larkspur</div>
      <div class="sponsor"><i></i>Venta</div>
      <div class="sponsor">Quillmark</div>
      <div class="sponsor">Horizonte</div>
      <div class="sponsor"><i></i>Fennick</div>
      <div class="sponsor"><i></i>Fennick</div>
      <div class="sponsor">Horizonte</div>
      <div class="sponsor"><i></i>Venta</div>
      <div class="sponsor">Larkspur</div>
      <div class="sponsor">Quillmark</div>
    </div>
  </div>
</section>

<footer class="footer">
  <div class="wrap">
    <div class="footer-brand">
      <span class="brand-mark"></span>
      <span class="brand-name">TIDEWELL</span>
      <span class="brand-sub">Marigold Synchronized Swim Team</span>
    </div>
    <div class="footer-col col-contact">
      <h5>Contact Us</h5>
      <div class="contact-item"><svg width="12" height="12" viewBox="0 0 12 12"><path d="M2 1l2.5 0 1 3-1.5 1a7 7 0 0 0 3 3l1-1.5 3 1V11A10 10 0 0 1 1 2z" fill="#777"/></svg>(504)-555-0148 (Phone)</div>
      <div class="contact-item"><svg width="12" height="12" viewBox="0 0 12 12"><rect x="1" y="4" width="10" height="6" fill="#777"/><rect x="3" y="1" width="6" height="3" fill="#777"/></svg>(504)-555-0149 (Fax)</div>
      <div class="contact-item"><svg width="12" height="10" viewBox="0 0 14 11"><rect x="0.5" y="0.5" width="13" height="10" fill="none" stroke="#777"/><path d="M1 1l6 5 6-5" fill="none" stroke="#777"/></svg><a>info@tidewellclub.com</a></div>
      <div class="contact-item"><svg width="10" height="13" viewBox="0 0 10 13"><path d="M5 12C2 8 1 6 1 4.5a4 4 0 0 1 8 0C9 6 8 8 5 12z" fill="#777"/><circle cx="5" cy="4.5" r="1.5" fill="#f5f6f7"/></svg>#254 Magazine Street,<br>New Orleans, LA</div>
    </div>
    <div class="footer-col col-news">
      <h5>Newsletter</h5>
      <p>Register your email address to get information about us</p>
      <div class="field">Email Address</div>
      <span class="btn-small">Subscribe</span>
    </div>
    <div class="footer-col col-follow">
      <h5>Follow Us</h5>
      <p>Follow the team for show photos, practice news and fun moments from the pool.</p>
      <div class="follow-icons"><span></span><span></span><span></span><span></span><span></span></div>
    </div>
  </div>
</footer>
<div class="copyright">© Copyright 2016 Tidewell LLC. All Rights Reserved</div>

</body>
</html>
```